Cybersecurity Company Profile Word Template

We are looking for designs to develop a modern, innovative, and Company Profile template. This template will be a Word template that we will convert to PDF and send to potential clients and partners. The ideal structure of the template can be found below. We would like to see designs that relate to cybersecurity and include our company colors white, black, and red (#A80402). We have attached the logo we plan to use as we are rebranding. Additionally, I have included our logo variations. Company website is https://vornelquay.io. For content placeholder text is fine. We are concerned with the overall template having the necessary sections, pages, and overall structure we have mentioned in this brief.

Ideal template flow and structure:
-Cover Page
-Company "Contact Us"
-Table of Contents
-About Company
- NAICS Codes
- 541519 - Other Computer Related Servcies
- 541512 - Computer Systems Design Services
- 541690 - Other Scientific and Technical Consulting Services
- 541511 - Custom Computer Programming Services
-CEO Statement/Message (picture/headshot will be added to this page)
-Company History
-Vision and Misson
-Team Bios- Bio will include a picrure
-Our Values
- (Short paragraph)
- Our Services
- Penetration Testing
- Red Team/Threat Emulation
- Cloud Security Assessments
- Vulnerability Management
- Managed Detection and Response
- Incident Response
- Threat Hunting
- Risk Assessments
- Simulated Phishing Campaigns
- Projects

Target Market(s)

Potential customers and partners

Industry/Entity Type

Cybersecurity

Colors

Designer to choose colors to be used in the design.

Requirements
Must have
• Red must be #a80402

```html
<!DOCTYPE html>
<html lang="en">
<head>
<meta charset="utf-8">
<title>Vornel Quay Security — Company Profile</title>
<link href="https://fonts.googleapis.com/css2?family=Archivo+Black&family=Lato:wght@400;700&display=swap" rel="stylesheet">
<style>
:root{
  --red:#a80402;
  --ink:#111111;
  --dark:#2b2b2b;
  --grey-bg:#c9c9c9;
  --grey-card:#dcdcdf;
  --text:#6a6a6a;
  --paper:#ffffff;
}
*{margin:0;padding:0;box-sizing:border-box}
html,body{width:1200px;height:1142px;overflow:hidden}
body{background:var(--grey-bg);font-family:'Lato',sans-serif;color:var(--text);position:relative}
.page{position:absolute;width:259px;height:336px;background:var(--paper);overflow:hidden}
.header{position:absolute;left:0;top:0;width:259px;height:40px}
.brand-text{font-family:'Lato',sans-serif;font-size:5.4px;font-weight:700;letter-spacing:.6px;fill:var(--ink)}
.page-title{position:absolute;left:27px;top:40px;font-family:'Archivo Black',sans-serif;font-size:7.6px;line-height:9.5px;letter-spacing:.9px;color:var(--ink);text-transform:uppercase}
.page-title .accent{color:var(--red);display:block}
.page-no{position:absolute;left:225px;top:320px;width:5px;height:5px;background:var(--red);color:#fff;font-size:3px;line-height:5px;text-align:center;font-weight:700}
.body-copy{position:absolute;font-size:4.3px;line-height:8.4px;text-align:justify;color:var(--text)}
.body-copy p+p{margin-top:8.4px}
.photo{position:absolute}

/* cover */
.cover{background:linear-gradient(180deg,#2e2e2e 0%,#1d1d1d 100%)}
.cover-brand{position:absolute;left:64px;top:30px;display:flex;align-items:center;gap:5px}
.cover-brand .mark{width:22px;height:22px;border-radius:50%;background:var(--red)}
.cover-brand .name{font-size:10px;letter-spacing:2px;color:#fff;font-weight:400}
.cover-art{left:20px;top:112px;width:219px;height:170px;background:radial-gradient(ellipse at 50% 55%,#e01410 0%,#7a0605 35%,#2a0a0a 65%,transparent 80%)}
.cover-address{position:absolute;left:20px;top:308px;font-size:6px;color:#fff;display:flex;align-items:center;gap:4px}

/* toc */
.toc-title{position:absolute;left:33px;top:29px;font-size:11px;color:var(--ink);font-weight:400;letter-spacing:.2px}
.toc-list{position:absolute;left:33px;top:51px;width:192px;list-style:none}
.toc-list li{display:flex;justify-content:space-between;font-size:4.6px;line-height:9.75px;color:var(--ink);font-weight:700}
.toc-list li.sub{padding-left:9px;font-weight:400}

/* naics */
.naics-row{position:absolute;left:27px;width:203px;height:19px;border-radius:10px;background:var(--dark);display:flex;overflow:hidden}
.naics-code{width:46px;color:#fff;font-size:6px;font-weight:700;display:flex;align-items:center;justify-content:center}
.naics-name{flex:1;background:var(--red);color:#fff;border-radius:10px;font-size:5.2px;font-weight:700;display:flex;align-items:center;justify-content:center}

/* ceo */
.ceo-band{position:absolute;left:104px;top:91px;width:128px;height:17px;background:var(--dark);color:#fff;font-size:6px;display:flex;align-items:center;justify-content:center}
.ceo-role{position:absolute;left:104px;top:112px;width:128px;text-align:center;font-size:6px;line-height:7px;color:var(--ink)}

/* history */
.side-band{position:absolute;left:0;top:0;width:27px;height:307px;background:var(--red)}
.history-box{position:absolute;left:27px;top:184px;width:203px;height:123px;background:var(--dark)}

/* mission */
.mission-box{position:absolute;left:27px;top:40px;width:203px;height:127px;background:var(--red);clip-path:polygon(0 0,188px 0,203px 15px,203px 100%,0 100%)}
.block-head{font-family:'Archivo Black',sans-serif;font-size:7px;letter-spacing:.8px;text-transform:uppercase}
.mission-box .block-head{position:absolute;left:10px;top:6px;color:#fff}
.mission-box .body-copy{left:10px;top:19px;width:183px;color:#fff;line-height:8.5px}
.vision-head{position:absolute;left:38px;top:173px;color:var(--ink)}
.vision-row{position:absolute;left:27px;width:203px;color:#fff}
.vision-row .icon{position:absolute;left:2px;top:3px;width:14px;height:14px;background:#fff;display:flex;align-items:center;justify-content:center}
.vision-row h4{position:absolute;left:24px;top:3px;font-size:5.4px;font-weight:400}
.vision-row p{position:absolute;left:24px;top:13px;width:173px;font-size:4.2px;line-height:5.9px;text-align:justify}
.vision-row.red{background:var(--red)}
.vision-row.dark{background:var(--dark)}

/* team */
.bio-card{position:absolute;width:59px;height:89px;border-radius:30px;text-align:center}
.bio-card.red{background:var(--red);color:#fff}
.bio-card.grey{background:var(--grey-card);color:var(--ink)}
.bio-card .headshot{position:absolute;left:5px;top:5px;width:49px;height:49px;border-radius:50%;background:#fff}
.bio-card .headshot span{position:absolute;left:9px;top:9px;width:31px;height:31px;border-radius:50%;background:var(--ink)}
.bio-card .who{position:absolute;left:0;top:57px;width:59px;font-size:4.4px;line-height:6px}

/* services */
.service-tag{position:absolute;left:27px;display:flex;align-items:center}
.service-tag .badge{width:14px;height:14px;border-radius:50%;background:var(--red);border:1.5px solid #5a0000;position:relative;z-index:1;display:flex;align-items:center;justify-content:center}
.service-tag .label{background:var(--red);color:#fff;font-size:5.4px;height:11px;line-height:11px;padding:0 6px 0 8px;margin-left:-4px;border-radius:0 6px 6px 0}
</style>
</head>
<body>

<!-- 1 Cover -->
<section class="page cover" style="left:41px;top:34px">
  <div class="cover-brand"><span class="mark"></span><span class="name">VORNEL QUAY</span></div>
  <div class="photo cover-art" role="img" aria-label="Red glowing digital padlock on a circuit board beneath a red roof outline"></div>
  <div class="cover-address">
    <svg width="5" height="7" viewBox="0 0 10 14"><path d="M5 0a5 5 0 0 0-5 5c0 4 5 9 5 9s5-5 5-9a5 5 0 0 0-5-5zm0 7a2 2 0 1 1 0-4 2 2 0 0 1 0 4z" fill="#fff"/></svg>
    2184 Harlow Ave. #310, Marlin Bay, Florida 33091
  </div>
  <svg style="position:absolute;left:0;top:300px" width="259" height="24"><polyline points="0,18 202,18 210,9 259,9" fill="none" stroke="var(--red)" stroke-width="0.7"/></svg>
</section>

<!-- 2 Table of contents -->
<section class="page" style="left:329px;top:34px">
  <h1 class="toc-title">TABLE OF CONTENTS</h1>
  <ul class="toc-list">
    <li><span>Why Vornel Quay Security?</span><span>03</span></li>
    <li><span>NAICS Codes</span><span>04</span></li>
    <li><span>CEO Statement Message</span><span>05</span></li>
    <li><span>Company History</span><span>06</span></li>
    <li><span>Mission &amp; Vision</span><span>07</span></li>
    <li><span>Team Bios</span><span>08</span></li>
    <li><span>Our Values</span><span>09</span></li>
    <li><span>Our Services</span><span>10</span></li>
    <li class="sub"><span>Penetration Testing</span><span>10</span></li>
    <li class="sub"><span>Red Team/Threat Emulation</span><span>10</span></li>
    <li class="sub"><span>Cloud Security Assessments</span><span>10</span></li>
    <li class="sub"><span>Vulnerability Management</span><span>11</span></li>
    <li class="sub"><span>Managed Detection and Response</span><span>11</span></li>
    <li class="sub"><span>Incident Response</span><span>11</span></li>
    <li class="sub"><span>Threat Hunting</span><span>11</span></li>
    <li class="sub"><span>Risk Assessments</span><span>12</span></li>
    <li class="sub"><span>Simulated Phishing Campaigns</span><span>12</span></li>
    <li class="sub"><span>Projects</span><span>12</span></li>
  </ul>
</section>

<!-- 3 Why -->
<section class="page" style="left:615px;top:34px">
  <svg class="header" viewBox="0 0 259 40"><polyline points="0,28 164,28 176,17 259,17" fill="none" stroke="var(--red)" stroke-width="0.6"/><circle cx="177" cy="27" r="5" fill="var(--red)"/><text class="brand-text" x="185" y="29">VORNEL QUAY</text></svg>
  <h2 class="page-title">Why<span class="accent">Vornel Quay Security?</span></h2>
  <div class="body-copy" style="left:27px;top:66px;width:203px"><p>As we become more and more dependent on connectivity and applications, businesses must evolve and stay ahead of the game with innovative security practices. Cybersecurity threats will continue to challenge businesses of all sizes and it is critical for organizations to protect their assets and data. Our goal is to mitigate these attacks by helping you quickly detect and respond to threats utilizing our security assessment services. Let us partner with you to help identify weaknesses in your organization's security posture.</p></div>
  <svg style="position:absolute;left:27px;top:168px" width="203" height="140"><polygon points="0,0 180,0 203,20 203,140 196,140 196,23 178,4 0,4" fill="var(--red)"/></svg>
  <div class="photo" style="left:27px;top:172px;width:196px;height:135px;background:linear-gradient(120deg,#1a1a1a,#6b6b6b 55%,#2a2a2a)" role="img" aria-label="Two colleagues reviewing a tablet in front of a wall of data screens, black and white"></div>
  <div class="page-no">3</div>
</section>

<!-- 4 NAICS -->
<section class="page" style="left:902px;top:34px">
  <svg class="header" viewBox="0 0 259 40"><polyline points="0,28 164,28 176,17 259,17" fill="none" stroke="var(--red)" stroke-width="0.6"/><circle cx="177" cy="27" r="5" fill="var(--red)"/><text class="brand-text" x="185" y="29">VORNEL QUAY</text></svg>
  <h2 class="page-title">NAICS<span class="accent">Codes</span></h2>
  <div class="naics-row" style="top:97px"><span class="naics-code">541519</span><span class="naics-name">Other Computer Related Servcies</span></div>
  <div class="naics-row" style="top:131px"><span class="naics-code">541512</span><span class="naics-name">Computer Systems Design Services</span></div>
  <div class="naics-row" style="top:165px"><span class="naics-code">541690</span><span class="naics-name">Other Scientific and Technical Consulting Services</span></div>
  <div class="naics-row" style="top:199px"><span class="naics-code">541511</span><span class="naics-name">Custom Computer Programming Services</span></div>
  <div class="page-no">4</div>
</section>

<!-- 5 CEO -->
<section class="page" style="left:41px;top:402px">
  <svg class="header" viewBox="0 0 259 40"><polyline points="0,28 164,28 176,17 259,17" fill="none" stroke="var(--red)" stroke-width="0.6"/><circle cx="177" cy="27" r="5" fill="var(--red)"/><text class="brand-text" x="185" y="29">VORNEL QUAY</text></svg>
  <h2 class="page-title">CEO Statement<span class="accent">Message</span></h2>
  <svg style="position:absolute;left:27px;top:81px" width="78" height="74"><polygon points="10,0 77,0 77,62 65,73 0,73 0,10" fill="var(--dark)" stroke="var(--red)" stroke-width="1.5"/></svg>
  <div class="photo" style="left:40px;top:92px;width:52px;height:52px;border-radius:50%;background:#f2f2f2" role="img" aria-label="CEO headshot placeholder"></div>
  <div class="ceo-band">CEO NAME HERE</div>
  <div class="ceo-role">CEO DESIGNATION<br>HERE</div>
  <div class="body-copy" style="left:27px;top:167px;width:203px">
    <p>Lorem Ipsum is simply dummy text of the printing and typesetting industry. Lorem Ipsum has been the industry's standard dummy text ever since the 1500s, when an unknown printer took a galley of type and scrambled it to make a type specimen book.</p>
    <p>It has survived not only five centuries, but also the leap into electronic typesetting, remaining essentially unchanged. It was popularised in the 1960s with the release of Marlowe sheets containing Lorem Ipsum passages, and more recently with desktop publishing software like Quillset Layout including versions of Lorem Ipsum.</p>
    <p>It has survived not only five centuries, but also the leap into electronic typesetting, remaining essentially unchanged.</p>
  </div>
  <div class="page-no">5</div>
</section>

<!-- 6 Company history -->
<section class="page" style="left:329px;top:402px">
  <div class="side-band"></div>
  <svg class="header" viewBox="0 0 259 40"><polyline points="27,28 164,28 176,17 259,17" fill="none" stroke="var(--red)" stroke-width="0.6"/><circle cx="177" cy="27" r="5" fill="var(--red)"/><text class="brand-text" x="185" y="29">VORNEL QUAY</text></svg>
  <h2 class="page-title" style="left:32px">Company<span class="accent">History</span></h2>
  <div class="photo" style="left:27px;top:83px;width:156px;height:78px;background:linear-gradient(90deg,#7a7a7a,#d8d8d8 60%,#f0f0f0);clip-path:polygon(0 0,100% 0,100% 88%,94% 100%,0 100%)" role="img" aria-label="Profile of a person in glasses overlaid with digital interface graphics and a city skyline, black and white"></div>
  <div class="history-box"></div>
  <div class="body-copy" style="left:36px;top:200px;width:185px;color:#e6e6e6"><p>Lorem Ipsum is simply dummy text of the printing and typesetting industry. Lorem Ipsum has been the industry's standard dummy text ever since the 1500s, when an unknown printer took a galley of type and scrambled it to make a type specimen book. It has survived not only five centuries, but also the leap into electronic typesetting, remaining essentially unchanged. It was popularised in the 1960s with the release of Marlowe sheets containing Lorem Ipsum passages, and more recently with desktop publishing software like Quillset Layout including versions of Lorem Ipsum.</p></div>
  <div class="page-no">6</div>
</section>

<!-- 7 Mission & vision -->
<section class="page" style="left:615px;top:402px">
  <svg class="header" viewBox="0 0 259 40"><polyline points="0,28 164,28 176,17 259,17" fill="none" stroke="var(--red)" stroke-width="0.6"/><circle cx="177" cy="27" r="5" fill="var(--red)"/><text class="brand-text" x="185" y="29">VORNEL QUAY</text></svg>
  <div class="mission-box">
    <h3 class="block-head">Misson</h3>
    <div class="body-copy"><p>Founded in Marlin Bay, FL vornel quay security is a provider of cybersecurity consulting services with a focus on penetration testing, threat detection, vulnerability management, and compliance. Our mission is to be proactive, intelligent, and secure in protecting your sensitive assets. We provide in-depth security assessments for small to medium-sized businesses across the country. Our certified professional engineers have years of experience identifying vulnerabilities, penetration testing, and proactively hunting for threats. With new security threats emerging every day, we understand the importance of securing your organization. We know the IT industry and how quickly technology can evolve. At vornel quay security, we pride ourselves in staying abreast of the latest tactics, techniques, and procedures used by advanced adversaries to help keep your business secure.</p></div>
  </div>
  <h3 class="block-head vision-head">Visson</h3>
  <div class="vision-row red" style="top:187px;height:38px;clip-path:polygon(0 0,193px 0,203px 8px,203px 100%,0 100%)">
    <span class="icon"><svg width="9" height="9" viewBox="0 0 10 10"><circle cx="4" cy="4" r="3" fill="none" stroke="#111" stroke-width="1"/><line x1="6.2" y1="6.2" x2="9.5" y2="9.5" stroke="#111" stroke-width="1"/></svg></span>
    <h4>Managed Detection and Response</h4>
    <p>Our <b>MDR services</b> also include proactive incident response, regular risk assessments, and comprehensive reporting. With our Managed Detection and Response services, you can trust that we will help keep your business safe and secure.</p>
  </div>
  <div class="vision-row dark" style="top:229px;height:42px">
    <span class="icon"><svg width="9" height="9" viewBox="0 0 10 10"><circle cx="5" cy="3.5" r="2.5" fill="#111"/><path d="M0.5 10c0-3 2-4.5 4.5-4.5S9.5 7 9.5 10z" fill="#111"/></svg></span>
    <h4>Red Team Attack Simulation</h4>
    <p><b>Red Team Attack Simulation services</b> are tailored to your needs and help you ensure that your system is secure and able to withstand malicious cyber attacks. With our assistance, you can rest assured that your network is protected and your data is safe.</p>
  </div>
  <div class="vision-row red" style="top:271px;height:36px">
    <span class="icon"><svg width="9" height="9" viewBox="0 0 10 10"><polygon points="5,0.5 9.7,9.5 0.3,9.5" fill="#111"/><rect x="4.5" y="3.5" width="1" height="3.5" fill="#fff"/><rect x="4.5" y="7.6" width="1" height="1" fill="#fff"/></svg></span>
    <h4>Risk and Compliance</h4>
    <p><b>Comprehensive risk and compliance services</b> are designed to reduce the risk of data breaches, protect your customers' data, and provide you with the peace of mind that your business is secure.</p>
  </div>
  <div class="page-no">7</div>
</section>

<!-- 8 Team bios -->
<section class="page" style="left:902px;top:402px">
  <svg class="header" viewBox="0 0 259 40"><polyline points="0,28 164,28 176,17 259,17" fill="none" stroke="var(--red)" stroke-width="0.6"/><circle cx="177" cy="27" r="5" fill="var(--red)"/><text class="brand-text" x="185" y="29">VORNEL QUAY</text></svg>
  <h2 class="page-title">Team<span class="accent">Bios</span></h2>
  <div class="bio-card red" style="left:27px;top:78px"><div class="headshot" role="img" aria-label="Team member headshot placeholder"><span></span></div><div class="who">NAME HERE<br>Designation Here</div></div>
  <div class="bio-card grey" style="left:99px;top:78px"><div class="headshot" role="img" aria-label="Team member headshot placeholder"><span></span></div><div class="who">NAME HERE<br>Designation Here</div></div>
  <div class="bio-card red" style="left:171px;top:78px"><div class="headshot" role="img" aria-label="Team member headshot placeholder"><span></span></div><div class="who">NAME HERE<br>Designation Here</div></div>
  <div class="bio-card grey" style="left:27px;top:183px"><div class="headshot" role="img" aria-label="Team member headshot placeholder"><span></span></div><div class="who" style="color:#fff">NAME HERE<br>Designation Here</div></div>
  <div class="bio-card red" style="left:99px;top:183px"><div class="headshot" role="img" aria-label="Team member headshot placeholder"><span></span></div><div class="who">NAME HERE<br>Designation Here</div></div>
  <div class="bio-card grey" style="left:171px;top:183px"><div class="headshot" role="img" aria-label="Team member headshot placeholder"><span></span></div><div class="who">NAME HERE<br>Designation Here</div></div>
  <div class="page-no">8</div>
</section>

<!-- 9 Our value -->
<section class="page" style="left:41px;top:771px">
  <svg class="header" viewBox="0 0 259 40"><polyline points="0,28 164,28 176,17 259,17" fill="none" stroke="var(--red)" stroke-width="0.6"/><circle cx="177" cy="27" r="5" fill="var(--red)"/><text class="brand-text" x="185" y="29">VORNEL QUAY</text></svg>
  <h2 class="page-title">Our<span class="accent">Value</span></h2>
  <div class="photo" style="left:27px;top:69px;width:203px;height:140px;background:linear-gradient(135deg,#9a9a9a,#d4d4d4 50%,#8a8a8a)" role="img" aria-label="Woman in a VR headset surrounded by security interface icons, black and white"></div>
  <svg style="position:absolute;left:27px;top:69px" width="203" height="140"><polyline points="1,0 1,118 22,139 203,139" fill="none" stroke="var(--red)" stroke-width="2"/></svg>
  <div class="body-copy" style="left:27px;top:224px;width:203px"><p>Lorem Ipsum is simply dummy text of the printing and typesetting industry. Lorem Ipsum has been the industry's standard dummy text ever since the 1500s, when an unknown printer took a galley of type and scrambled it to make a type specimen book. It has survived not only five centuries, but also the leap into electronic typesetting, remaining essentially unchanged. It was popularised in the 1960s with the release of Marlowe sheets containing Lorem Ipsum passages, and more recently with desktop publishing software like Quillset Layout including versions of Lorem Ipsum.</p></div>
  <div class="page-no">9</div>
</section>

<!-- 10 Services -->
<section class="page" style="left:329px;top:771px">
  <svg class="header" viewBox="0 0 259 40"><polyline points="0,28 164,28 176,17 259,17" fill="none" stroke="var(--red)" stroke-width="0.6"/><circle cx="177" cy="27" r="5" fill="var(--red)"/><text class="brand-text" x="185" y="29">VORNEL QUAY</text></svg>
  <h2 class="page-title">Our<span class="accent">Service</span></h2>
  <div class="service-tag" style="top:70px"><span class="badge"><svg width="7" height="7"><circle cx="3.5" cy="3.5" r="2.6" fill="none" stroke="#fff" stroke-width="1"/></svg></span><span class="label">Penetration Testing</span></div>
  <div class="body-copy" style="left:27px;top:89px;width:203px"><p>External Penetration Testing is a process that involves several stages, including reconnaissance, scanning, and exploitation. During the reconnaissance stage, the tester gathers information about the target and creates a profile. In the scanning stage, the tester uses specialized tools and techniques to identify open ports and services and potential vulnerabilities. During the exploitation stage, the tester attempts to exploit these vulnerabilities and evaluate the potential impact. With our external penetration testing, you can be confident that your data and systems are secure.</p></div>
  <div class="service-tag" style="top:164px"><span class="badge"><svg width="7" height="7"><circle cx="3.5" cy="3.5" r="2.6" fill="none" stroke="#fff" stroke-width="1"/></svg></span><span class="label">Red Team/Threat Emulation</span></div>
  <div class="body-copy" style="left:27px;top:183px;width:203px"><p>A Red Team is a group of security professionals who simulate an attacker's perspective, tactics, and tools in order to identify and exploit vulnerabilities in an organization's security infrastructure. Red Teams use a combination of technical, operational, and strategic expertise to replicate the methods of real-world attackers, providing organizations with a realistic assessment of their security posture.</p></div>
  <div class="service-tag" style="top:242px"><span class="badge"><svg width="7" height="7"><circle cx="3.5" cy="3.5" r="2.6" fill="none" stroke="#fff" stroke-width="1"/></svg></span><span class="label">Cloud Security Assessments</span></div>
  <div class="body-copy" style="left:27px;top:261px;width:203px"><p>Cloud security assessments and testing are the processes of evaluating the security of cloud environments to identify and fix any vulnerabilities. The goal is to ensure that the cloud environment is secure and that sensitive information is protected.</p></div>
  <div class="page-no">10</div>
</section>

<!-- 11 Services continued -->
<section class="page" style="left:615px;top:771px">
  <svg class="header" viewBox="0 0 259 40"><polyline points="0,28 164,28 176,17 259,17" fill="none" stroke="var(--red)" stroke-width="0.6"/><circle cx="177" cy="27" r="5" fill="var(--red)"/><text class="brand-text" x="185" y="29">VORNEL QUAY</text></svg>
  <div class="service-tag" style="top:42px"><span class="badge"><svg width="7" height="7"><circle cx="3.5" cy="3.5" r="2.6" fill="none" stroke="#fff" stroke-width="1"/></svg></span><span class="label">Vulnerability Management</span></div>
  <div class="body-copy" style="left:27px;top:60px;width:203px"><p>In today's digital age, organizations of all sizes are becoming increasingly dependent on technology and the internet to conduct their business. This dependence has made the need for robust cybersecurity measures a top priority, as the consequences of a security breach can be devastating. One of the key components of an effective cybersecurity strategy is vulnerability management. At Vornel Quay Security LLC, we understand the importance of Vulnerability Management.</p></div>
  <div class="service-tag" style="top:125px"><span class="badge"><svg width="7" height="7"><circle cx="3.5" cy="3.5" r="2.6" fill="none" stroke="#fff" stroke-width="1"/></svg></span><span class="label">Managed Detection and Response</span></div>
  <div class="body-copy" style="left:27px;top:143px;width:203px"><p>With the increasing use of endpoints and the growing number of security threats, traditional endpoint security solutions are no longer adequate. Managed Endpoint Detection and Response provides a more comprehensive approach to endpoint security, allowing organizations to detect and respond to threats in real-time.</p></div>
  <div class="service-tag" style="top:191px"><span class="badge"><svg width="7" height="7"><circle cx="3.5" cy="3.5" r="2.6" fill="none" stroke="#fff" stroke-width="1"/></svg></span><span class="label">Incident Response</span></div>
  <div class="body-copy" style="left:27px;top:209px;width:203px"><p>Lorem Ipsum is simply dummy text of the printing and typesetting industry. Lorem Ipsum has been the industry's standard dummy text ever since the 1500s, when an unknown printer took a galley of type and scrambled it to make a type specimen book.</p></div>
  <div class="service-tag" style="top:250px"><span class="badge"><svg width="7" height="7"><circle cx="3.5" cy="3.5" r="2.6" fill="none" stroke="#fff" stroke-width="1"/></svg></span><span class="label">Threat Hunting</span></div>
  <div class="body-copy" style="left:27px;top:268px;width:203px"><p>With the increasing sophistication of cyber-attacks and the growing number ofsecurity threats, traditional security solutions are no longer adequate. Threat Hunting provides a more proactive approach to security, allowing organizations to detect and respond to threats before they cause significant damage.</p></div>
  <div class="page-no">11</div>
</section>

<!-- 12 Services continued -->
<section class="page" style="left:902px;top:771px">
  <svg class="header" viewBox="0 0 259 40"><polyline points="0,28 164,28 176,17 259,17" fill="none" stroke="var(--red)" stroke-width="0.6"/><circle cx="177" cy="27" r="5" fill="var(--red)"/><text class="brand-text" x="185" y="29">VORNEL QUAY</text></svg>
  <div class="service-tag" style="top:43px"><span class="badge"><svg width="7" height="7"><circle cx="3.5" cy="3.5" r="2.6" fill="none" stroke="#fff" stroke-width="1"/></svg></span><span class="label">Risk Assessments</span></div>
  <div class="body-copy" style="left:27px;top:61px;width:203px"><p>Risk and Compliance Readiness refers to the ability of an organization to identify, assess, and manage risks and comply with relevant regulations and standards. In today's rapidly changing business environment, organizations must be prepared to manage a wide range of risks, including cyber threats, data breaches, and regulatory changes. By being risk and compliance ready, organizations can ensure that they are able to operate effectively and minimize the impact of adverse events. We offer a comprehensive suite of services to ensure your organization is compliant with all applicable regulations, from developing an effective security policy to training staff on security protocols.</p></div>
  <div class="service-tag" style="top:141px"><span class="badge"><svg width="7" height="7"><circle cx="3.5" cy="3.5" r="2.6" fill="none" stroke="#fff" stroke-width="1"/></svg></span><span class="label">Simulated Phishing</span></div>
  <div class="body-copy" style="left:27px;top:159px;width:203px"><p>Phishing is a type of social engineering attack that involves tricking individuals into revealing sensitive information, such as passwords or financial information, through the use of fake emails, websites, or phone calls. Phishing is a major threat to organizations and individuals, as it can result in data breaches, financial losses, and reputational damage.</p></div>
  <div class="service-tag" style="top:203px"><span class="badge"><svg width="7" height="7"><circle cx="3.5" cy="3.5" r="2.6" fill="none" stroke="#fff" stroke-width="1"/></svg></span><span class="label">Projects</span></div>
  <div class="body-copy" style="left:27px;top:221px;width:203px"><p>Phishing is a type of social engineering attack that involves tricking individuals into revealing sensitive information, such as passwords or financial information, through the use of fake emails, websites, or phone calls. Phishing is a major threat to organizations and individuals, as it can result in data breaches, financial losses, and reputational damage.</p></div>
  <div class="page-no">12</div>
</section>

</body>
</html>
```